Pinecrest Harbor Foundation Web Design

The design we need is for a WordPress blog that will be our content platform. We are a registered 501(c)3 non-profit that focuses on financially supporting the treatment of cancer patients that have been told they have no hope and there is nothing the conventional medical system can do for them. Through this wesbite we want to both rasie awareness about the treatment options plus, raise funds for treating patients. The two primary target audiences of the site are...

1. Terminally ill patients and their families to let them know that there is an option other then hospice and that we are hear to support that option.

2. People looking to help donate to a worthwhile cause that resonates with them.

The website is https://pinecrestharborfoundation.org/

See attached logo designs!!!

Target Market(s)

Cancer patients and their families

Industry/Entity Type

Foundation

Font styles to use
Sans Serif

Colors
ffffff
fbed22

Requirements
Must have
• I like this look of this site. It is clean, simple, helpful, soft. I like the flow of the pages.
• http://www.meadowsforcalm.org/
• I like the design and flow but NOT the color or boldness
• https://tvbn-youth.org/
• I like this style for a donation page.
• https://www.tumorstudyhub.org/we-are-tsh/join-the-cause/donations/one-time-donation
• with the addition of a Would you like your employer to match? button.
Nice to have
• White black and gold - but soft
• Even possibly grayscale like the site I like.

```html
<!DOCTYPE html>
<html lang="en">
<head>
<meta charset="utf-8">
<title>Pinecrest Harbor Foundation</title>
<link href="https://fonts.googleapis.com/css2?family=Lato:ital,wght@0,400;0,700;1,400&display=swap" rel="stylesheet">
<style>
:root{
  --white:#ffffff;
  --ink:#222222;
  --text:#555555;
  --muted:#8a8a8a;
  --gold:#ecc84f;
  --charcoal:#545454;
  --mid-gray:#6e6e6e;
  --light-gray:#bdbdbd;
  --line:#d9d9d9;
  --mist:#ececec;
}
*{box-sizing:border-box;margin:0;padding:0}
html,body{width:1200px;height:3758px;overflow:hidden;background:var(--white);font-family:'Lato',sans-serif;color:var(--text)}
.page{position:relative;width:1200px;height:3758px}
.abs{position:absolute}

/* header */
.brand{left:88px;top:30px;width:250px;font-size:22px;font-weight:700;color:var(--ink);line-height:1.15;letter-spacing:.5px}
.nav{top:58px;left:400px;display:flex;font-size:15px;color:#777;letter-spacing:.5px;white-space:nowrap}
.nav span{margin-right:30px}
.nav span:last-child{margin-right:0}
.nav .current{color:var(--ink)}
.search{left:1080px;top:56px}

/* hero */
.hero{left:0;top:120px;width:1132px;height:519px;background:linear-gradient(90deg,#cfd2d6 0%,#dfe1e4 35%,#eeeeef 100%)}
.hero-photo{left:500px;top:0;width:632px;height:519px;background:radial-gradient(circle at 45% 40%,#eadfd6 0%,#d9d2cf 45%,#cfd1d5 100%)}
.hero-title{left:93px;top:145px;color:var(--ink)}
.hero-title .small{font-size:30px;font-weight:700;letter-spacing:.5px}
.hero-title .big{font-size:38px;font-weight:700;line-height:48px;letter-spacing:.5px}
.btn{display:flex;align-items:center;justify-content:center;border-radius:30px;font-size:16px;font-weight:700}
.btn-dark{left:93px;top:306px;width:152px;height:42px;background:#333;color:var(--white)}
.dots{left:556px;top:480px;display:flex;gap:10px}
.dots i{width:14px;height:14px;border-radius:50%;background:#9a9a9a;border:2px solid var(--white)}

/* mission */
.mission{left:0;top:639px;width:1200px;height:401px;background:linear-gradient(180deg,#e8e8e8 0%,#f6f6f6 45%,#ececec 100%)}
.section-title{width:100%;text-align:center;font-size:32px;font-weight:700;color:var(--ink);letter-spacing:.5px}
.mission .section-title{top:95px}
.mission-copy{top:160px;width:100%;text-align:center;font-size:17px;line-height:28px;color:var(--text)}
.btn-outline{left:544px;top:285px;width:155px;height:48px;border:2px solid #888;color:#333;background:var(--white)}

/* why */
.why-panel{left:0;top:1040px;width:601px;height:455px;background:var(--charcoal);color:var(--white)}
.why-panel h2{position:absolute;left:108px;top:77px;font-size:28px;font-weight:700;letter-spacing:.5px}
.why-panel p{position:absolute;left:108px;width:460px;font-size:16px;line-height:27px;color:#eee}
.btn-light{left:108px;top:300px;width:153px;height:45px;background:var(--white);color:#333}
.why-photo{left:601px;top:1040px;width:599px;height:455px;background:linear-gradient(120deg,#c9ccd2 0%,#e4e6ea 50%,#aeb6c2 100%)}

/* how */
.how-title{top:1525px;font-size:28px;font-weight:400}
.ring{width:300px;height:300px;border-radius:50%;border:3px solid #b9b9b9;display:flex;align-items:center;justify-content:center;background:var(--white)}
.disc{width:268px;height:268px;border-radius:50%;display:flex;align-items:center;justify-content:center;text-align:center;color:var(--white);font-size:21px;line-height:27px;font-weight:700;padding-top:60px}

/* story */
.story{left:80px;top:1946px;width:1037px;height:451px;background:linear-gradient(90deg,#8a6e6e 0%,#6f4744 45%,#7b3a3a 100%)}
.story h2{position:absolute;top:105px;width:100%;text-align:center;color:var(--white);font-size:30px;font-weight:700}
.story blockquote{position:absolute;top:165px;left:200px;width:637px;text-align:center;color:#f3eaea;font-style:italic;font-size:19px;line-height:32px}
.avatars{left:406px;top:300px;display:flex;gap:8px}
.avatars i{width:50px;height:50px;border-radius:50%;background:#d8cbc6;border:2px solid var(--white)}

/* stars */
.stars-title{top:2450px}
.star-card{top:2515px;width:335px;height:331px;background:#ccc}
.star-head{height:60px;background:#2b2b2b;color:var(--white);font-size:23px;font-weight:700;display:flex;align-items:center;justify-content:center}
.star-photo{height:271px}
.star-text{position:absolute;top:80px;left:40px;width:255px;text-align:center;color:var(--white);font-size:15px;line-height:24px}
.read-more{position:absolute;left:100px;top:232px;width:135px;height:32px;background:var(--gold);color:var(--white);font-size:13px;font-weight:700;display:flex;align-items:center;justify-content:center}

/* blogs + signup */
.box{top:2906px;height:358px;border:2px solid var(--line);background:var(--white)}
.box h3{position:absolute;left:38px;top:32px;font-size:21px;font-weight:400;color:#444;letter-spacing:.5px}
.date{left:38px;width:70px;height:70px;text-align:center;color:var(--white)}
.date b{display:block;height:44px;background:#cfcfcf;font-size:30px;font-weight:400;line-height:44px}
.date span{display:block;height:26px;background:#8f8f8f;font-size:14px;line-height:26px}
.post{left:132px;width:340px}
.post h4{font-size:16px;font-weight:400;color:#333;margin-bottom:6px}
.post p{font-size:12px;line-height:17px;color:#888}
.post em{display:block;font-style:normal;font-size:13px;color:#666;margin-top:10px;letter-spacing:.5px}
.signup .sub{position:absolute;left:33px;top:72px;font-size:13px;color:#888}
.field{left:33px;width:425px;height:40px;border:1px solid #ccc;font-size:14px;color:#666;padding:10px 12px}
.subscribe{left:33px;top:270px;width:165px;height:40px;background:var(--gold);color:var(--white);font-size:14px;font-weight:700;display:flex;align-items:center;justify-content:center}

/* footer */
.footer{left:0;top:3269px;width:1200px;height:413px;background:linear-gradient(180deg,#e4e4e4 0%,#f2f2f2 40%,#e9e9e9 100%)}
.col{top:3400px}
.col h5{font-size:22px;font-weight:400;color:#333;margin-bottom:22px;letter-spacing:.5px}
.col p{font-size:16px;color:#666;line-height:35px}
.divider{top:3405px;width:1px;height:180px;background:#cfcfcf}
.social{display:flex;gap:10px}
.social i{width:44px;height:44px;border-radius:50%;border:2px solid #333}
.bottom{left:0;top:3682px;width:1200px;height:76px;background:var(--white);text-align:center;font-size:14px;color:#777;line-height:76px}
</style>
</head>
<body>
<div class="page">

  <header>
    <div class="abs brand">Pinecrest Harbor Foundation</div>
    <nav class="abs nav"><span class="current">HOME</span><span>ABOUT US</span><span>WHAT WE DO</span><span>SERVICES</span><span>TESTIMONIAL</span><span>CONTACT</span></nav>
    <svg class="abs search" width="22" height="22" viewBox="0 0 22 22"><circle cx="9" cy="9" r="6.5" fill="none" stroke="#444" stroke-width="2.5"/><line x1="14" y1="14" x2="20" y2="20" stroke="#444" stroke-width="2.5"/></svg>
  </header>

  <section class="abs hero">
    <div class="abs hero-photo" role="img" aria-label="Smiling young woman embracing an older woman in a pink headscarf wearing a pink ribbon"></div>
    <div class="abs hero-title">
      <div class="small">WE HELP CANCER PATIENTS</div>
      <div class="big">FINANCIALLY FOR<br>THIER TREATMENT</div>
    </div>
    <div class="abs btn btn-dark">Learn More</div>
    <div class="abs dots"><i></i><i></i><i></i><i></i></div>
  </section>

  <section class="abs mission" role="region" aria-label="Our mission">
    <h2 class="abs section-title">OUR MISSION</h2>
    <p class="abs mission-copy">Vivamus porttitor purus nisi eleifend libero a tempus libero lectus feugiat felis vlacus<br><span style="display:block;height:9px"></span>mollis aliquam Curabitur iaculis tempus eros Curabitur vel mi sit amet magna malesuada ultrices<br>Ut nisi erat fermentum vel congue id euismod in elit Fusce ultricies orci ac feugiat</p>
    <div class="abs btn btn-outline">Learn More</div>
  </section>

  <section class="abs why-panel">
    <h2>WHY WE ARE</h2>
    <p style="top:127px">Vivamus porttitor purus nisi eleifend libero a tempus libero lectus feugiat felis vlacus Ut ac mi quis lacus mollis aliquam Curabitur iaculis tempus</p>
    <p style="top:223px">eros Curabitur vel mi sit amet magna malesuada ultrices Ut nisi erat fermentum vel congue</p>
    <div class="abs btn btn-light">Learn More</div>
  </section>
  <div class="abs why-photo" role="img" aria-label="Doctor with a tablet talking to a patient in a hospital bed"></div>

  <h2 class="abs section-title how-title">HOW WE WORK</h2>
  <div class="abs ring" style="left:150px;top:1586px"><div class="disc" style="background:var(--mid-gray)">Find Patient<br>Who need help</div></div>
  <div class="abs ring" style="left:455px;top:1586px"><div class="disc" style="background:var(--gold)">Collect Donation<br>for Patient</div></div>
  <div class="abs ring" style="left:760px;top:1586px"><div class="disc" style="background:var(--light-gray)">Help Cancer Patient<br>in their Treatment</div></div>

  <section class="abs story" role="img" aria-label="Smiling child in a pink headscarf behind a success story quote">
    <h2>SUCCESS STORY</h2>
    <blockquote>“Morbi diam mauris viverra in gravida eu mattis in ante Morbi eget arcu Morbi porta libero id ullamcorper nonummy nibh ligula pulvinar metus eget consectetuer augue nisi quis ”</blockquote>
    <div class="abs avatars"><i></i><i></i><i></i><i></i></div>
    <svg class="abs" style="left:70px;top:200px" width="30" height="60" viewBox="0 0 30 60"><polyline points="26,2 4,30 26,58" fill="none" stroke="#fff" stroke-width="2"/></svg>
    <svg class="abs" style="left:937px;top:200px" width="30" height="60" viewBox="0 0 30 60"><polyline points="4,2 26,30 4,58" fill="none" stroke="#fff" stroke-width="2"/></svg>
  </section>

  <h2 class="abs section-title stars-title">OUR STARS</h2>
  <div class="abs star-card" style="left:83px">
    <div class="star-head">Patient Name</div>
    <div class="star-photo" role="img" aria-label="Woman in a blue headscarf resting her head on her arms" style="background:linear-gradient(135deg,#dfe6ec,#b9c6d3)"></div>
  </div>
  <div class="abs star-card" style="left:433px">
    <div class="star-head">Patient Name</div>
    <div class="star-photo" role="img" aria-label="Patient portrait under a dark overlay" style="background:linear-gradient(135deg,#5b5650,#3f3b37)"></div>
    <p class="star-text">Her family found hope again after our fund covered six months of care at a clinic near home</p>
    <div class="read-more">READ MORE</div>
  </div>
  <div class="abs star-card" style="left:784px">
    <div class="star-head">Patient Name</div>
    <div class="star-photo" role="img" aria-label="Smiling young child after chemotherapy" style="background:linear-gradient(135deg,#f0e4de,#cf9fae)"></div>
  </div>

  <section class="abs box" style="left:83px;width:511px">
    <h3>RECENT  BLOGS</h3>
    <div class="abs date" style="top:95px"><b>02</b><span>OCT</span></div>
    <div class="abs post" style="top:95px"><h4>Etiam eu urna Sed porta Suspe</h4><p>Small grants help families cover travel and care costs during treatment</p><em>READ MORE</em></div>
    <div class="abs date" style="top:220px"><b>08</b><span>OCT</span></div>
    <div class="abs post" style="top:220px"><h4>Ut nisi erat fermentum vel congue</h4><p>Meet the volunteers who keep our patient support line open every day</p><em>READ MORE</em></div>
  </section>

  <section class="abs box signup" style="left:606px;width:511px">
    <h3 style="left:33px">SIGN UP HERE FOR ANY HELP</h3>
    <p class="sub">Tell us how we can support you today</p>
    <div class="abs field" style="top:108px">First Name</div>
    <div class="abs field" style="top:160px">Last Name</div>
    <div class="abs field" style="top:212px">Email address</div>
    <div class="abs subscribe">SUBSCRIBE</div>
  </section>

  <footer>
    <div class="abs footer" role="img" aria-label="Soft grey mountain landscape"></div>
    <div class="abs col" style="left:108px"><h5>QUICK LINKS</h5><p>Home<br>About Us<br>What We Do<br>Why Us</p></div>
    <div class="abs divider" style="left:295px"></div>
    <div class="abs col" style="left:356px"><h5>SUBLINKS</h5><p>Cancer Patients<br>Donate Now<br>Success Stories<br>Blogs</p></div>
    <div class="abs divider" style="left:560px"></div>
    <div class="abs col" style="left:624px"><h5>RESOURCES</h5><p>Sitemap<br>Term of Use<br>Contact Us</p></div>
    <div class="abs divider" style="left:800px"></div>
    <div class="abs col" style="left:864px"><h5>FOLLOW US</h5><div class="social"><i></i><i></i><i></i><i></i></div></div>
    <div class="abs bottom">© 2017 Company Name  All right reserved  Term of Use</div>
  </footer>

</div>
</body>
</html>
```